Business Cards for a law firm

Business cards for our law firm. Use our silhoette logo and OAK PARTNERS - check our website (www.oakpartners.example)

Contact Information for Business Card

our silhouette logo, OAK PARTNERS, 800-555-0147, Dorian Pemberton, dorian@oakpartners.example

Requirements
Must have
• our silhouette logo, OAK PARTNERS, 800-555-0147, Dorian Pemberton, dorian@oakpartners.example

```html
<!DOCTYPE html>
<html lang="en">
<head>
<meta charset="utf-8">
<title>Oak Partners – Business Cards</title>
<link rel="stylesheet" href="https://fonts.googleapis.com/css2?family=Montserrat:wght@500&family=Arimo:wght@400&display=swap">
<style>
  :root {
    --navy: #172f63;
    --paper: #ffffff;
    --backdrop: #d9d9dc;
    --rule: rgba(255,255,255,0.75);
    --ink-light: #ffffff;
  }
  * { margin: 0; padding: 0; box-sizing: border-box; }
  html, body { width: 1200px; height: 800px; overflow: hidden; }
  body {
    background: var(--backdrop);
    display: flex;
    align-items: center;
    justify-content: center;
    gap: 60px;
  }
  .card {
    width: 520px;
    height: 297px;
    border-radius: 22px;
    position: relative;
    overflow: hidden;
  }
  .card--back { background: var(--navy); color: var(--ink-light); }
  .card--front { background: var(--paper); }

  .card__mark {
    position: absolute;
    right: 44px;
    top: 52px;
    font-family: "Montserrat", sans-serif;
    font-weight: 500;
    font-size: 17px;
    letter-spacing: 0.14em;
    color: var(--ink-light);
  }
  .card__rule {
    position: absolute;
    left: 26px;
    right: 30px;
    top: 190px;
    height: 1px;
    background: var(--rule);
  }
  .card__name {
    position: absolute;
    left: 30px;
    top: 160px;
    font-family: "Montserrat", sans-serif;
    font-weight: 500;
    font-size: 19px;
    font-variant: small-caps;
    letter-spacing: 0.06em;
  }
  .contact {
    position: absolute;
    left: 34px;
    top: 202px;
    list-style: none;
    font-family: "Arimo", sans-serif;
    font-size: 14.5px;
    line-height: 21px;
  }
  .contact li { display: flex; align-items: center; gap: 9px; }
  .contact svg { width: 11px; height: 11px; flex: none; }

  .brand {
    position: absolute;
    left: 60px;
    top: 50%;
    transform: translateY(-50%);
    display: flex;
    align-items: center;
    gap: 14px;
  }
  .brand__dot {
    width: 34px;
    height: 34px;
    background: var(--navy);
  }
  .brand__name {
    font-family: "Montserrat", sans-serif;
    font-weight: 500;
    font-size: 36px;
    letter-spacing: 0.12em;
    color: var(--navy);
  }
</style>
</head>
<body>
  <section class="card card--back">
    <div class="card__mark">OAK PARTNERS</div>
    <div class="card__name">Dorian Pemberton</div>
    <div class="card__rule"></div>
    <ul class="contact">
      <li>
        <svg viewBox="0 0 12 12" aria-hidden="true"><path d="M2.5 1 L4.5 1 L5 3.5 L3.8 4.5 Q5 7 7.5 8.2 L8.5 7 L11 7.5 L11 9.5 Q11 11 9.5 11 Q1 10 1 2.5 Q1 1 2.5 1Z" fill="#fff"/></svg>
        800-555-0147
      </li>
      <li>
        <svg viewBox="0 0 12 12" aria-hidden="true"><rect x="0.5" y="2" width="11" height="8" fill="#fff"/><path d="M0.5 2 L6 6.5 L11.5 2" fill="none" stroke="#172f63" stroke-width="1"/></svg>
        dorian@oakpartners.example
      </li>
      <li>
        <svg viewBox="0 0 12 12" aria-hidden="true"><circle cx="6" cy="6" r="5.5" fill="#fff"/><path d="M0.5 6 H11.5 M6 0.5 Q3 6 6 11.5 M6 0.5 Q9 6 6 11.5" fill="none" stroke="#172f63" stroke-width="0.8"/></svg>
        www.oakpartners.example
      </li>
    </ul>
  </section>

  <section class="card card--front">
    <div class="brand">
      <span class="brand__dot"></span>
      <span class="brand__name">OAK PARTNERS</span>
    </div>
  </section>
</body>
</html>
```